Webdesign für Bedrucken Papiertaschen, Schildern etc.
Zielgruppe
Wir bedrucken Papiertaschen, Papierbeutel, Laternen, Aluplaketten, Schilder, etc. und lasern Hundemarken. Zielgruppen von Privat bis Geschäftskunden
Aufgabenstellung
Der Shop sollte ein einfacher und kostengünstiger 'Printhafen'-shop werden. Wo die Kunden anhand von einem Editor Ihre Logos oder Druckvorlagen selber hochladen und/oder gestalten könne. Bisher haben die Kunden eifach ihre Bidldatei per E-Mail geschickt und wir haben diese dann weiter verarbeit.
Der Shop sollte, wenn möglich, günstig im Unterhalt sein, da wir nicht abschätzen können, wie gut diese laufen wird.
Wir haben wie 3 Bereich: 1. Papierbeutel/Taschen / 2. Stallplaketten (für z.B. Pferdesport) / 3. Diverses (Wie z.B. die Laternen, Schilder, Hundemarken, etc.)
Es würde sich um eine separate Webseite handeln. Daher ist bei Design freie Hand, eifach und klar... auch für nicht so ambitionierte Privatkunden oder kleine Unternehmen.

```html
<!DOCTYPE html>
<html lang="de">
<head>
<meta charset="utf-8">
<title>Printhafen – Editor</title>
<link href="https://fonts.googleapis.com/css2?family=Inter:wght@400;500;600;700;800&display=swap" rel="stylesheet">
<style>
:root{
  --stage:#c2c2c2;
  --page:#f7f8fa;
  --white:#ffffff;
  --ink:#0b111c;
  --ink-soft:#4b5563;
  --muted:#6b7280;
  --line:#e5e7eb;
  --lime:#c2f05a;
  --lime-soft:#e8f9c4;
  --lime-text:#a3d930;
  --canvas:#eef1f5;
  --red:#ef4444;
  --foot-text:#a4acb9;
}
*{box-sizing:border-box;margin:0;padding:0}
html,body{width:1007px;height:1200px;overflow:hidden;background:var(--stage)}
body{font-family:"Inter",sans-serif;color:var(--ink)}
.scale{position:absolute;left:0;top:0;width:1763px;height:2100px;transform:scale(0.5712);transform-origin:0 0}
.abs{position:absolute}
.page{left:134px;top:118px;width:1492px;height:1878px;background:var(--page);overflow:hidden}
.hero-band{left:0;top:0;width:1492px;height:310px;background:linear-gradient(#ffffff,#f4f6f8 40%);border-bottom:1px solid var(--line)}
.navbar{left:126px;top:25px;width:1238px;height:54px;background:var(--white);border-radius:28px;box-shadow:0 2px 8px rgba(0,0,0,.05)}
.brand{font-weight:800;font-size:34px;letter-spacing:-1px;display:flex;align-items:center;gap:8px}
.brand-dot{width:14px;height:14px;background:var(--lime);border-radius:3px}
.nav-link{font-size:15px;font-weight:500;color:var(--ink)}
.nav-active{border-bottom:2px solid var(--lime);padding-bottom:4px}
.btn-dark{background:var(--ink);color:#fff;border-radius:20px;font-weight:600;display:flex;align-items:center;justify-content:center;gap:8px}
.eyebrow{font-size:12px;font-weight:600;letter-spacing:3px;color:var(--lime-text)}
.headline{font-size:52px;font-weight:800;letter-spacing:-2px;line-height:1}
.headline span{color:var(--ink-soft)}
.lead{font-size:16.5px;line-height:24px;color:var(--ink-soft);width:670px}
.mode-switch{left:1005px;top:234px;width:351px;height:44px;background:var(--white);border:1px solid var(--line);border-radius:22px}
.label{font-size:10.5px;font-weight:600;letter-spacing:1.3px;color:#374151}
.editor{left:134px;top:343px;width:1222px;height:785px;background:var(--white);border-radius:20px;border:1px solid var(--line);box-shadow:0 4px 16px rgba(0,0,0,.04);overflow:hidden}
.tool{background:var(--white);border:1px solid var(--line);border-radius:12px;display:flex;flex-direction:column;align-items:center;justify-content:center;gap:6px;font-size:11.5px;font-weight:600}
.tool.lime{background:var(--lime);border-color:var(--lime)}
.sw{width:26px;height:26px;border-radius:50%}
.layer{left:16px;width:225px;height:33px;border-radius:10px;display:flex;align-items:center;gap:10px;padding-left:8px;font-size:12.5px;font-weight:500}
.layer i{font-style:normal;width:18px;height:18px;border:1px solid var(--line);border-radius:4px;font-size:11px;display:flex;align-items:center;justify-content:center}
.layer.active{background:var(--lime-soft);border:1px solid #b8e86a}
.pill-btn{border-radius:10px;font-size:12.5px;font-weight:600;display:flex;align-items:center;justify-content:center;gap:6px}
.field{background:var(--white);border:1px solid var(--line);border-radius:10px;font-size:12.5px;display:flex;align-items:center;padding-left:10px}
.dot{width:27px;height:27px;border-radius:50%}
.card{top:1218px;width:396px;height:170px;background:var(--white);border:1px solid var(--line);border-radius:20px}
.card-icon{left:23px;top:24px;width:40px;height:40px;border-radius:50%;background:var(--ink);display:flex;align-items:center;justify-content:center}
.card h3{position:absolute;left:23px;top:80px;font-size:17px;font-weight:700}
.card p{position:absolute;left:23px;top:106px;width:355px;font-size:14.5px;line-height:20px;color:var(--ink-soft)}
.footer{left:0;top:1496px;width:1492px;height:382px;background:var(--ink);color:#fff}
.foot-col h4{font-size:15px;font-weight:700;margin-bottom:20px}
.foot-col a{display:block;font-size:15px;color:var(--foot-text);text-decoration:none;margin-bottom:15px}
.contact-row{display:flex;gap:12px;font-size:15px;color:var(--foot-text);line-height:20px;margin-bottom:12px}
</style>
</head>
<body>
<div class="scale">
<div class="abs page">

  <div class="abs hero-band"></div>

  <header class="abs navbar">
    <div class="abs brand" style="left:20px;top:8px">Printhafen<span class="brand-dot"></span></div>
    <span class="abs nav-link nav-active" style="left:713px;top:17px">Produkte</span>
    <span class="abs nav-link" style="left:801px;top:17px">Editor</span>
    <span class="abs nav-link" style="left:868px;top:17px">Beispiel</span>
    <span class="abs nav-link" style="left:948px;top:17px">Kontakt</span>
    <div class="abs" style="left:1035px;top:10px;width:34px;height:34px;border:1px solid var(--line);border-radius:50%;display:flex;align-items:center;justify-content:center">
      <svg width="15" height="15" viewBox="0 0 16 16" fill="none" stroke="#0b111c" stroke-width="1.6"><circle cx="7" cy="7" r="5"/><path d="M11 11l3.5 3.5"/></svg>
    </div>
    <div class="abs btn-dark" style="left:1080px;top:9px;width:147px;height:36px;font-size:15px">Editor öffnen
      <svg width="10" height="10" viewBox="0 0 10 10" fill="none" stroke="#fff" stroke-width="1.6"><path d="M2 8L8 2M3 2h5v5"/></svg></div>
  </header>

  <div class="abs eyebrow" style="left:134px;top:148px">03 — EDITOR</div>
  <h1 class="abs headline" style="left:133px;top:172px">Echter Editor. <span>Echte Vorschau.</span></h1>
  <p class="abs lead" style="left:134px;top:230px">Logo platzieren, Text setzen, Vorder- und Rückseite. Oder fertige Druckdatei hochladen — wir prüfen sie persönlich.</p>

  <div class="abs mode-switch">
    <div class="abs btn-dark" style="left:2px;top:2px;width:172px;height:38px;font-size:15px">
      <svg width="16" height="16" viewBox="0 0 16 16" fill="none" stroke="#fff" stroke-width="1.5"><path d="M2 14L11 5M10 2v2M13 4h2M13 8v2M6 2h1"/></svg>Online gestalten</div>
    <div class="abs" style="left:195px;top:12px;font-size:15px;font-weight:600;display:flex;gap:8px;align-items:center">
      <svg width="16" height="16" viewBox="0 0 16 16" fill="none" stroke="#0b111c" stroke-width="1.5"><path d="M8 11V2M4.5 5.5L8 2l3.5 3.5M2 11v3h12v-3"/></svg>Datei hochladen</div>
  </div>

  <!-- Editor -->
  <section class="abs editor">
    <!-- left panel -->
    <div class="abs" style="left:0;top:0;width:258px;height:785px;border-right:1px solid var(--line)">
      <div class="abs label" style="left:16px;top:14px">HINZUFÜGEN</div>
      <div class="abs tool" style="left:16px;top:36px;width:109px;height:63px">
        <svg width="16" height="16" viewBox="0 0 16 16" fill="none" stroke="#0b111c" stroke-width="1.5"><path d="M3 3h10M8 3v11M6 14h4"/></svg>Text</div>
      <div class="abs tool" style="left:132px;top:36px;width:109px;height:63px">
        <svg width="16" height="16" viewBox="0 0 16 16" fill="none" stroke="#0b111c" stroke-width="1.5"><rect x="2" y="2" width="12" height="12" rx="2"/><circle cx="6" cy="6" r="1.3"/><path d="M3 13l4-4 3 3 2-2 2 2"/></svg>Bild</div>
      <div class="abs tool" style="left:16px;top:106px;width:109px;height:63px">
        <svg width="16" height="16" viewBox="0 0 16 16" fill="none" stroke="#0b111c" stroke-width="1.5"><rect x="2.5" y="2.5" width="11" height="11" rx="1.5"/></svg>Form</div>
      <div class="abs tool lime" style="left:132px;top:106px;width:109px;height:63px">
        <svg width="16" height="16" viewBox="0 0 16 16" fill="none" stroke="#0b111c" stroke-width="1.5"><path d="M8 11V2M4.5 5.5L8 2l3.5 3.5M2 11v3h12v-3"/></svg>Upload</div>
      <div class="abs" style="left:0;top:181px;width:258px;border-top:1px solid var(--line)"></div>
      <div class="abs label" style="left:16px;top:195px">HINTERGRUND</div>
      <div class="abs sw" style="left:17px;top:218px;background:#fff;border:2px solid var(--lime)"></div>
      <div class="abs sw" style="left:51px;top:218px;background:#f3e9dc;border:1px solid var(--line)"></div>
      <div class="abs sw" style="left:85px;top:218px;background:var(--ink)"></div>
      <div class="abs sw" style="left:118px;top:218px;background:#fdf1c7;border:1px solid var(--line)"></div>
      <div class="abs sw" style="left:152px;top:218px;background:#dce8fb;border:1px solid var(--line)"></div>
      <div class="abs" style="left:0;top:257px;width:258px;border-top:1px solid var(--line)"></div>
      <div class="abs label" style="left:16px;top:272px;display:flex;gap:6px;align-items:center">
        <svg width="13" height="13" viewBox="0 0 16 16" fill="none" stroke="#374151" stroke-width="1.5"><path d="M8 2l6 3-6 3-6-3zM2 8l6 3 6-3M2 11l6 3 6-3"/></svg>EBENEN (4)</div>
      <div class="abs layer" style="top:295px"><i>T</i>1.2 kg · natürlich · sch...</div>
      <div class="abs layer active" style="top:332px"><i>T</i>Premium</div>
      <div class="abs layer" style="top:369px"><i>□</i>Form</div>
      <div class="abs layer" style="top:406px"><i>T</i>WOLLPFOTE</div>
    </div>

    <!-- center -->
    <div class="abs" style="left:258px;top:0;width:687px;height:785px;background:var(--canvas)">
      <div class="abs" style="left:0;top:0;width:687px;height:52px;background:var(--white);border-bottom:1px solid var(--line)"></div>
      <div class="abs" style="left:17px;top:12px;width:182px;height:29px;background:#eef0f3;border-radius:10px"></div>
      <div class="abs pill-btn" style="left:19px;top:14px;width:93px;height:25px;background:#fff;box-shadow:0 1px 2px rgba(0,0,0,.08);border-radius:8px">Vorderseite</div>
      <div class="abs pill-btn" style="left:115px;top:14px;width:80px;height:25px;color:var(--muted);font-weight:500">Rückseite</div>
      <div class="abs" style="left:211px;top:16px;height:20px;border-left:1px solid var(--line)"></div>
      <svg class="abs" style="left:232px;top:19px" width="15" height="15" viewBox="0 0 16 16" fill="none" stroke="#0b111c" stroke-width="1.5"><path d="M5 4L2 7l3 3M2 7h8a4 4 0 010 8H8"/></svg>
      <svg class="abs" style="left:271px;top:19px" width="15" height="15" viewBox="0 0 16 16" fill="none" stroke="#0b111c" stroke-width="1.5"><path d="M11 4l3 3-3 3M14 7H6a4 4 0 000 8h2"/></svg>
      <div class="abs pill-btn" style="left:304px;top:11px;width:94px;height:31px;background:var(--lime-soft)">
        <svg width="13" height="13" viewBox="0 0 16 16" fill="none" stroke="#0b111c" stroke-width="1.5"><rect x="2" y="2" width="12" height="12"/><path d="M6 2v12M10 2v12M2 6h12M2 10h12"/></svg>Hilfslinien</div>
      <div class="abs" style="left:464px;top:11px;width:118px;height:31px;border:1px solid var(--line);border-radius:10px"></div>
      <svg class="abs" style="left:473px;top:19px" width="15" height="15" viewBox="0 0 16 16" fill="none" stroke="#0b111c" stroke-width="1.5"><circle cx="7" cy="7" r="5"/><path d="M11 11l3.5 3.5M5 7h4"/></svg>
      <div class="abs" style="left:506px;top:19px;font-size:12.5px;font-weight:600">100%</div>
      <svg class="abs" style="left:561px;top:19px" width="15" height="15" viewBox="0 0 16 16" fill="none" stroke="#0b111c" stroke-width="1.5"><circle cx="7" cy="7" r="5"/><path d="M11 11l3.5 3.5M5 7h4M7 5v4"/></svg>
      <div class="abs pill-btn" style="left:592px;top:12px;width:79px;height:29px;background:var(--ink);color:#fff;font-weight:500">Vorschau</div>

      <div class="abs" style="left:175px;top:163px;font-size:11px;color:#374151">210 × 297 mm · 3 mm Beschnitt</div>
      <div class="abs" style="left:175px;top:181px;width:337px;height:476px;background:#fff;box-shadow:0 6px 20px rgba(15,23,42,.12)">
        <div class="abs" style="left:7px;top:7px;width:323px;height:461px;border:1px dashed #f4b6c4"></div>
        <div class="abs" style="left:19px;top:19px;width:299px;height:437px;border:1px dashed #f1e7a6"></div>
        <div class="abs" style="left:31px;top:91px;font-size:11px;font-weight:700;letter-spacing:.3px">WOLLPF</div>
        <div class="abs" style="left:74px;top:47px;width:94px;height:94px;border-radius:50%;background:var(--lime)"></div>
        <div class="abs" style="left:-50px;top:409px;width:200px;text-align:center;font-size:8px;color:#374151">1.2 kg · natürlich · schweizer herkunft</div>
      </div>
      <div class="abs" style="left:104px;top:472px;width:242px;height:54px;border:2px solid var(--ink);display:flex;align-items:center;justify-content:center;text-align:center;font-size:22px;font-weight:700;line-height:25px">Premium<br>Hauptfutter</div>
      <div class="abs" style="left:100px;top:468px;width:8px;height:8px;border-radius:50%;background:var(--ink)"></div>
      <div class="abs" style="left:339px;top:468px;width:8px;height:8px;border-radius:50%;background:var(--ink)"></div>
      <div class="abs" style="left:100px;top:519px;width:8px;height:8px;border-radius:50%;background:var(--ink)"></div>
      <div class="abs" style="left:339px;top:519px;width:8px;height:8px;border-radius:50%;background:var(--ink)"></div>

      <div class="abs" style="left:17px;top:742px;width:250px;height:27px;background:#fff;border-radius:14px;box-shadow:0 1px 3px rgba(0,0,0,.08);font-size:11.5px;font-weight:500;display:flex;align-items:center;gap:7px;padding-left:11px">
        <span style="width:6px;height:6px;border-radius:50%;background:var(--lime)"></span>Live · Vorderseite · Druckbereich sichtbar</div>
    </div>

    <!-- right panel -->
    <div class="abs" style="left:945px;top:0;width:277px;height:785px;border-left:1px solid var(--line)">
      <div class="abs" style="left:15px;top:21px;font-size:12.5px;font-weight:600;letter-spacing:1.5px;color:#374151">TEXT</div>
      <svg class="abs" style="left:203px;top:21px" width="14" height="14" viewBox="0 0 16 16" fill="none" stroke="#374151" stroke-width="1.4"><rect x="5" y="5" width="9" height="9" rx="1.5"/><path d="M11 5V3a1 1 0 00-1-1H3a1 1 0 00-1 1v7a1 1 0 001 1h2"/></svg>
      <svg class="abs" style="left:239px;top:21px" width="14" height="14" viewBox="0 0 16 16" fill="none" stroke="#ef4444" stroke-width="1.5"><path d="M2 4h12M6 4V2h4v2M4 4l1 10h6l1-10M7 7v5M9 7v5"/></svg>
      <div class="abs" style="left:0;top:55px;width:277px;border-top:1px solid var(--line)"></div>
      <div class="abs label" style="left:15px;top:80px">TEXT</div>
      <div class="abs field" style="left:15px;top:101px;width:246px;height:64px;align-items:flex-start;padding-top:9px;line-height:16px">Premium<br>Hauptfutter</div>
      <div class="abs label" style="left:15px;top:201px">SCHRIFT</div>
      <div class="abs field" style="left:15px;top:222px;width:246px;height:32px">Space Grotesk
        <svg style="position:absolute;right:10px" width="10" height="10" viewBox="0 0 10 10" fill="none" stroke="#0b111c" stroke-width="1.4"><path d="M2 4l3 3 3-3"/></svg></div>
      <div class="abs label" style="left:15px;top:283px">GRÖSSE</div>
      <div class="abs label" style="left:144px;top:283px">GEWICHT</div>
      <div class="abs field" style="left:15px;top:304px;width:117px;height:33px">22</div>
      <div class="abs field" style="left:144px;top:304px;width:117px;height:33px">Bold</div>
      <div class="abs label" style="left:15px;top:366px">AUSRICHTUNG</div>
      <div class="abs" style="left:15px;top:387px;width:246px;height:33px;border:1px solid var(--line);border-radius:10px"></div>
      <div class="abs" style="left:100px;top:389px;width:77px;height:29px;background:#eef1f5;border-radius:8px"></div>
      <svg class="abs" style="left:50px;top:397px" width="13" height="13" viewBox="0 0 14 14" stroke="#374151" stroke-width="1.3"><path d="M1 3h12M1 7h8M1 11h10"/></svg>
      <svg class="abs" style="left:132px;top:397px" width="13" height="13" viewBox="0 0 14 14" stroke="#0b111c" stroke-width="1.3"><path d="M1 3h12M3 7h8M2 11h10"/></svg>
      <svg class="abs" style="left:214px;top:397px" width="13" height="13" viewBox="0 0 14 14" stroke="#374151" stroke-width="1.3"><path d="M1 3h12M5 7h8M3 11h10"/></svg>
      <div class="abs label" style="left:15px;top:448px">STIL</div>
      <div class="abs pill-btn" style="left:15px;top:469px;width:32px;height:32px;background:var(--lime-soft);border:1px solid #b8e86a;color:var(--lime-text)">B</div>
      <div class="abs pill-btn" style="left:51px;top:469px;width:32px;height:32px;border:1px solid var(--line);font-style:italic;font-weight:400">I</div>
      <div class="abs label" style="left:15px;top:530px">FARBE</div>
      <div class="abs dot" style="left:16px;top:551px;background:var(--ink);box-shadow:0 0 0 2px #fff,0 0 0 4px var(--lime)"></div>
      <div class="abs dot" style="left:50px;top:551px;background:#6366f1"></div>
      <div class="abs dot" style="left:83px;top:551px;background:#22c55e"></div>
      <div class="abs dot" style="left:117px;top:551px;background:#ef4444"></div>
      <div class="abs dot" style="left:151px;top:551px;background:#f59e0b"></div>
      <div class="abs dot" style="left:184px;top:551px;background:#ec4899"></div>
      <div class="abs dot" style="left:218px;top:551px;background:#0ea5e9"></div>
      <div class="abs dot" style="left:16px;top:585px;background:#fff;border:1px solid var(--line)"></div>
      <div class="abs dot" style="left:50px;top:585px;border:1px dashed #9ca3af;display:flex;align-items:center;justify-content:center">
        <svg width="13" height="13" viewBox="0 0 16 16" fill="none" stroke="#374151" stroke-width="1.4"><path d="M8 2a6 6 0 000 12c1 0 1-1 1-2s1-1 2-1h1a2 2 0 002-2A6 6 0 008 2z"/><circle cx="5" cy="7" r=".8"/><circle cx="8" cy="5" r=".8"/><circle cx="11" cy="7" r=".8"/></svg></div>
      <div class="abs label" style="left:15px;top:640px">X (%)</div>
      <div class="abs label" style="left:144px;top:640px">Y (%)</div>
      <div class="abs field" style="left:15px;top:661px;width:117px;height:33px">50</div>
      <div class="abs field" style="left:144px;top:661px;width:117px;height:33px">72</div>
      <div class="abs label" style="left:15px;top:715px">BREITE (%)</div>
      <div class="abs label" style="left:144px;top:715px">ROTATION</div>
      <div class="abs field" style="left:15px;top:736px;width:117px;height:33px">70</div>
      <svg class="abs" style="left:144px;top:746px" width="12" height="12" viewBox="0 0 16 16" fill="none" stroke="#374151" stroke-width="1.6"><path d="M13 8a5 5 0 11-2-4M13 2v3h-3"/></svg>
      <div class="abs field" style="left:162px;top:736px;width:99px;height:33px">0</div>
    </div>
  </section>

  <!-- Feature cards -->
  <article class="abs card" style="left:134px">
    <div class="abs card-icon"><svg width="20" height="20" viewBox="0 0 16 16" fill="none" stroke="#c2f05a" stroke-width="1.4"><path d="M8 2l6 3-6 3-6-3zM2 8l6 3 6-3M2 11l6 3 6-3"/></svg></div>
    <h3>Vorder- &amp; Rückseite</h3>
    <p>Separate Layouts, eine Vorschau. Beidseitiger Druck in einem Flow.</p>
  </article>
  <article class="abs card" style="left:547px">
    <div class="abs card-icon"><svg width="18" height="18" viewBox="0 0 16 16" fill="none" stroke="#c2f05a" stroke-width="1.5"><path d="M3 3h10M8 3v11M6 14h4"/></svg></div>
    <h3>Profi-Typografie</h3>
    <p>Eigene Schriften, sauberes Kerning, Snap-to-grid für ausgerichtete Layouts.</p>
  </article>
  <article class="abs card" style="left:961px">
    <div class="abs card-icon"><svg width="20" height="20" viewBox="0 0 16 16" fill="none" stroke="#c2f05a" stroke-width="1.4"><path d="M8 2a6 6 0 000 12c1 0 1-1 1-2s1-1 2-1h1a2 2 0 002-2A6 6 0 008 2z"/><circle cx="5" cy="7" r=".8"/><circle cx="8" cy="5" r=".8"/><circle cx="11" cy="7" r=".8"/></svg></div>
    <h3>CMYK-genau</h3>
    <p>Farben werden in Druckraum konvertiert — kein böses Erwachen beim Andruck.</p>
  </article>

  <!-- Footer -->
  <footer class="abs footer">
    <div class="abs brand" style="left:136px;top:58px;color:#fff">Printhafen<span class="brand-dot"></span></div>
    <p class="abs" style="left:136px;top:114px;width:370px;font-size:15px;line-height:20px;color:var(--foot-text)">Druckprodukte online gestalten — Editor, Upload und persönliche Datenprüfung. Lokale Produktion in der Schweiz.</p>
    <div class="abs" style="left:136px;top:199px;width:150px;height:39px;background:var(--lime);color:var(--ink);border-radius:20px;font-size:15px;font-weight:600;display:flex;align-items:center;justify-content:center;gap:10px">Editor öffnen
      <svg width="10" height="10" viewBox="0 0 10 10" fill="none" stroke="#0b111c" stroke-width="1.6"><path d="M2 8L8 2M3 2h5v5"/></svg></div>
    <nav class="abs foot-col" style="left:643px;top:61px">
      <h4>Produkte</h4><a>Papierbeutel</a><a>Stallplaketten</a><a>Laternen</a><a>Hundemarken</a><a>Alle Produkte</a>
    </nav>
    <nav class="abs foot-col" style="left:814px;top:61px">
      <h4>Service</h4><a>Editor öffnen</a><a>Datei hochladen</a><a>Datenprüfung</a><a>Versand</a><a>Kontakt</a>
    </nav>
    <nav class="abs foot-col" style="left:985px;top:61px">
      <h4>Unternehmen</h4><a>Über uns</a><a>Druckpartner</a><a>Nachhaltigkeit</a><a>Impressum</a><a>Datenschutz</a>
    </nav>
    <div class="abs foot-col" style="left:1172px;top:61px">
      <h4>Kontakt</h4>
      <div class="contact-row" style="margin-top:-4px"><svg width="16" height="16" viewBox="0 0 16 16" fill="none" stroke="#c2f05a" stroke-width="1.4" style="margin-top:2px"><rect x="2" y="3.5" width="12" height="9" rx="1.5"/><path d="M2 5l6 4 6-4"/></svg>hallo@printhafen.ch</div>
      <div class="contact-row"><svg width="16" height="16" viewBox="0 0 16 16" fill="none" stroke="#c2f05a" stroke-width="1.4" style="margin-top:2px"><path d="M3 2h3l1 3-2 1a8 8 0 005 5l1-2 3 1v3a1 1 0 01-1 1A12 12 0 012 3a1 1 0 011-1z"/></svg>+41 44 512 80 90</div>
      <div class="contact-row"><svg width="16" height="16" viewBox="0 0 16 16" fill="none" stroke="#c2f05a" stroke-width="1.4" style="margin-top:2px"><path d="M8 15s5-4.5 5-8.5a5 5 0 00-10 0C3 10.5 8 15 8 15z"/><circle cx="8" cy="6.5" r="1.8"/></svg>Lindenweg 14<br>8000 Zürich</div>
    </div>
    <div class="abs" style="left:136px;top:310px;width:1222px;border-top:1px solid #1f2733"></div>
    <div class="abs" style="left:136px;top:335px;font-size:12.5px;color:var(--foot-text)">© 2026 Printhafen. Alle Rechte vorbehalten.</div>
    <div class="abs" style="left:1148px;top:335px;font-size:12.5px;color:var(--foot-text);display:flex;gap:24px"><span>Impressum</span><span>Datenschutz</span><span>AGB</span></div>
  </footer>

</div>
</div>
</body>
</html>
```